Dental Practice Billboard Design

We are a newer dental practice in need of a simple but appealing billboard for our growing dental practice to attract new patients. The practice is owned by husband and wife dentists and is family friendly in a small town in Kentucky. We try to be very friendly and caring to our patients. Would prefer a blue background for the billboard and our tooth logo to be prominent. We are partial to the Patua One font used in the image below but please feel free to tweak it as you deem necessary. The shape of the uppercase D and lowercase g are why we like that font, so fonts with a similarly shaped “D” and “g” would work as well. Please include our phone number (555) 847-1390. Please see our website Harlowbrookdentistry.example for more info on the practice if needed. Thank you! Looking forward to seeing your creation.
Updates

The dimensions will be 12ft x 24ft (3.6576m x 7.3152m). Apologies for not including this in the original prompt. Thank you all for your submissions.

Industry/Entity Type

Dental

Font styles to use
Other font styles liked:
• Patua One

Colors
0054AA
0677BA
7BADD7
CADEEF
E8F1F8
0094D4
00A9DD
6FCCEA
C7EBF8
E9F6FB
00AB8E
00BBA5
67D7C9
C6EFE9
E9F9F6
59FF00
82FF00
B8FF75
E3FFCB
F4FFEA

Requirements
Must have
• Phone number, website, Logo, Practice name “Harlow Brook Dentistry”
Should not have
• A tagline or slogan

```html
<!DOCTYPE html>
<html lang="en">
<head>
<meta charset="utf-8">
<title>Harlow Brook Dentistry Billboard</title>
<link href="https://fonts.googleapis.com/css2?family=Patua+One&display=swap" rel="stylesheet">
<style>
  :root {
    --navy: #06285a;
    --green: #19b11a;
    --white: #ffffff;
    --page: #ffffff;
  }
  * { margin: 0; padding: 0; box-sizing: border-box; }
  html, body { width: 1071px; height: 1200px; overflow: hidden; background: var(--page); }
  .canvas { position: relative; width: 1071px; height: 1200px; }
  .billboard {
    position: absolute; left: 38px; top: 363px;
    width: 995px; height: 473px;
    background: var(--navy);
    overflow: hidden;
    box-shadow: 0 2px 6px rgba(0,0,0,0.25);
    font-family: "Patua One", Georgia, serif;
    color: var(--white);
  }
  .band { position: absolute; inset: 0; width: 995px; height: 473px; }
  .brand-dot {
    position: absolute; left: 160px; top: 78px;
    width: 200px; height: 200px; border-radius: 50%;
    background: var(--green);
  }
  .practice-name { position: absolute; left: 385px; top: 52px; line-height: 1; }
  .practice-name .primary { display: block; font-size: 140px; margin-left: 18px; }
  .practice-name .secondary { display: block; font-size: 58px; margin-top: 4px; }
  .contact { position: absolute; right: 32px; list-style: none; display: flex; align-items: center; gap: 12px; }
  .contact svg { flex: none; }
  .contact.phone { top: 368px; font-size: 40px; }
  .contact.web { top: 424px; font-size: 31px; }
</style>
</head>
<body>
<div class="canvas">
  <section class="billboard" aria-label="Harlow Brook Dentistry billboard">
    <svg class="band" viewBox="0 0 995 473" aria-hidden="true">
      <path d="M0 400 C 250 420, 600 350, 995 354 L 995 473 L 0 473 Z" fill="#19b11a"/>
      <path d="M0 398 C 200 402, 380 385, 470 374 C 380 395, 200 408, 0 403 Z" fill="#19b11a"/>
      <path d="M510 368 C 650 345, 800 338, 880 336 C 780 342, 650 355, 520 372 Z" fill="#19b11a"/>
      <path d="M0 418 C 250 425, 550 380, 995 356 C 560 388, 250 432, 0 422 Z" fill="#06285a"/>
      <path d="M110 436 C 400 440, 650 395, 995 368 C 640 403, 400 446, 110 438 Z" fill="#06285a"/>
    </svg>

    <div class="brand-dot" aria-hidden="true"></div>

    <h1 class="practice-name">
      <span class="primary">Harlow</span>
      <span class="secondary">Brook Dentistry</span>
    </h1>

    <div class="contact phone">
      <svg width="40" height="40" viewBox="0 0 40 40" aria-hidden="true">
        <circle cx="20" cy="20" r="17.5" fill="none" stroke="#fff" stroke-width="3"/>
        <path d="M13 12 l4 -1 l2 5 l-2 2 c1 3 3 5 6 6 l2 -2 l5 2 l-1 4 c-9 1 -17 -7 -16 -16 z" fill="#fff"/>
      </svg>
      <span>(555) 847-1390</span>
    </div>

    <div class="contact web">
      <svg width="40" height="40" viewBox="0 0 40 40" aria-hidden="true">
        <circle cx="20" cy="20" r="17.5" fill="none" stroke="#fff" stroke-width="3"/>
        <circle cx="20" cy="20" r="11" fill="#fff"/>
        <path d="M14 15 c3 -1 5 1 4 3 c-1 2 2 3 1 6 c-2 -1 -4 -3 -5 -5 z M23 12 c2 1 5 4 4 8 c-2 0 -3 -2 -4 -3 z" fill="#19b11a"/>
      </svg>
      <span>Harlowbrookdentistry.example</span>
    </div>
  </section>
</div>
</body>
</html>
```